Stylish Business Cards Wanted

- DOUBLE SIDED Design Required -

High end, edgy cards for a corporate and personal stylist. Must include logo,
Name: Belinda Harwick
Title: Director and Stylist
telephone : +61 8 7142 5809
email: belinda@theloombriefing.example
website: theloombriefing.example
Tag: Corporate Workwear & Uniform Specialist | Personal Stylist
Would like nice icons for telephone, email, website

Target Market(s)

Businesses wanting stylish uniforms, people wanting stylish wardrobes

Industry/Entity Type

Corporate Workwear Stylist

Contact Information for Business Card

I would like black, white and gold foiling incorporated in the design - possibly a touch of the other colours on my branding guide attached Name: Belinda Harwick Title: Director and Stylist telephone : +61 8 7142 5809 email: belinda@theloombriefing.example website: theloombriefing.example Tag: Corporate Workwear & Uniform Specialist | Personal Stylist Would like nice icons for telephone, email, website

Font styles to use
Other font styles liked:
• Raleway

Colors

Designer to choose colors to be used in the design.

Requirements
Must have
• Gold foil accents

```html
<!DOCTYPE html>
<html lang="en">
<head>
<meta charset="utf-8">
<title>The Loom Briefing — Business Cards</title>
<link href="https://fonts.googleapis.com/css2?family=Montserrat:wght@400;500;700&family=Lato:wght@400&display=swap" rel="stylesheet">
<style>
  :root {
    --bg: #1b1e22;
    --card: #232323;
    --card-edge: #2c2c2c;
    --gold: #e2b23f;
    --gold-line: #b8902f;
    --white: #f2f2f2;
    --muted: #d6d6d6;
    --silver: #9a9a9a;
  }
  * { margin: 0; padding: 0; box-sizing: border-box; }
  html, body {
    width: 1200px; height: 900px; overflow: hidden;
    background: var(--bg);
  }
  .canvas {
    position: relative; width: 1200px; height: 900px;
    display: flex; flex-direction: column; align-items: center; justify-content: center; gap: 48px;
  }
  .card {
    position: relative; width: 640px; height: 366px;
    background: var(--card);
    border-radius: 26px;
    border: 1px solid var(--card-edge);
    box-shadow: 0 18px 40px rgba(0,0,0,.45);
    overflow: hidden;
  }

  /* Front */
  .front .brand {
    position: absolute; left: 48px; top: 44px;
    font-family: "Montserrat", sans-serif; font-weight: 500;
    font-size: 26px; line-height: 1.15; letter-spacing: .04em;
    color: var(--white);
  }
  .front .name-block {
    position: absolute; right: 48px; top: 150px; text-align: right;
  }
  .front .name {
    font-family: "Montserrat", sans-serif; font-weight: 700;
    font-size: 28px; letter-spacing: .03em; text-transform: uppercase;
    color: var(--gold);
  }
  .front .title {
    font-family: "Lato", sans-serif; font-size: 19px;
    color: var(--white); margin-top: 4px;
  }
  .front .divider {
    position: absolute; left: 48px; right: 48px; top: 238px;
    height: 1px; background: var(--gold-line);
  }
  .front .contacts {
    position: absolute; left: 48px; top: 256px;
    list-style: none;
    font-family: "Lato", sans-serif; font-size: 17px; color: var(--muted);
  }
  .front .contacts li { display: flex; align-items: center; gap: 10px; height: 27px; }
  .front .contacts svg { width: 15px; height: 15px; flex: none; }

  /* Back */
  .back .brand-large {
    position: absolute; left: 0; right: 0; top: 118px; text-align: center;
    font-family: "Montserrat", sans-serif; font-weight: 500;
    font-size: 52px; letter-spacing: .05em;
    color: var(--silver);
  }
  .back .tagline {
    position: absolute; left: 40px; right: 40px; bottom: 40px;
    font-family: "Montserrat", sans-serif; font-weight: 400;
    font-size: 14px; letter-spacing: .04em; text-transform: uppercase;
    color: var(--gold);
  }
</style>
</head>
<body>
<main class="canvas">
  <section class="card front" aria-label="Card front">
    <div class="brand">The Loom<br>Briefing</div>
    <div class="name-block">
      <div class="name">Belinda Harwick</div>
      <div class="title">Director and Stylist</div>
    </div>
    <div class="divider"></div>
    <ul class="contacts">
      <li>
        <svg viewBox="0 0 16 16" aria-hidden="true"><circle cx="8" cy="8" r="8" fill="var(--gold)"/><path d="M5.2 4.2l1.6-.4.8 2-1 .8a5 5 0 0 0 2.8 2.8l.8-1 2 .8-.4 1.6c-3.5.3-6.9-3.1-6.6-6.6z" fill="var(--card)"/></svg>
        +61 8 7142 5809
      </li>
      <li>
        <svg viewBox="0 0 16 16" aria-hidden="true"><circle cx="8" cy="8" r="8" fill="var(--gold)"/><rect x="4" y="5.2" width="8" height="5.6" rx=".6" fill="var(--card)"/><path d="M4.3 5.6L8 8.4l3.7-2.8" stroke="var(--gold)" stroke-width=".8" fill="none"/></svg>
        belinda@theloombriefing.example
      </li>
      <li>
        <svg viewBox="0 0 16 16" aria-hidden="true"><circle cx="8" cy="8" r="8" fill="var(--gold)"/><circle cx="8" cy="8" r="4.2" fill="none" stroke="var(--card)" stroke-width="1"/><path d="M3.8 8h8.4M8 3.8c-2 2.4-2 6 0 8.4M8 3.8c2 2.4 2 6 0 8.4" stroke="var(--card)" stroke-width=".9" fill="none"/></svg>
        www.theloombriefing.example
      </li>
    </ul>
  </section>

  <section class="card back" aria-label="Card back">
    <div class="brand-large">The Loom Briefing</div>
    <div class="tagline">Corporate Workwear | Uniform Specialist | Personal Stylist</div>
  </section>
</main>
</body>
</html>
```